Catalogue Design Project

We need a catalog design for a new private university called Redwell Institute Bayshore (see website www.rwi-bs.org). The catalog should be about 30 pages maximum and will include items such as General Information, Academic schedule, department descriptions, program descriptions, course descriptions, school policies, student services, admissions, San diego Lifestyle, etc.
I will provide the text but I need a professional design with regard to page layouts. I have provided some examples.
Ok, i posted the catalog content, just missing course descriptions.
Target Market(s)
Young Professionals, Foreign Students
Industry/Entity Type
University
Look and feel
Each slider illustrates characteristics of the customer's brand and the style your logo design should communicate.

```html
<!DOCTYPE html>
<html lang="en">
<head>
<meta charset="utf-8">
<title>Academic Programs – MBA Degree</title>
<link href="https://fonts.googleapis.com/css2?family=Carlito:ital,wght@0,400;0,700;1,400&display=swap" rel="stylesheet">
<style>
  :root{
    --ink:#1b1b1b;
    --blue:#2f5f98;
    --blue-dark:#1f4a7d;
    --blue-light:#5f8fc4;
    --accent-grey:#b4b8bd;
    --rule:#9aa9bd;
    --footer-ink:#8a8a8a;
    --paper:#ffffff;
    --page-tone-1:#efe6d2;
    --page-tone-2:#d9c9a6;
    --sky-tone:#dfe6ee;
  }
  *{margin:0;padding:0;box-sizing:border-box}
  html,body{width:927px;height:1200px;overflow:hidden;background:var(--paper)}
  body{font-family:"Carlito",Calibri,sans-serif;color:var(--ink)}
  .page{position:relative;width:927px;height:1200px;overflow:hidden;background:var(--paper)}

  .header-image{
    position:absolute;right:0;top:0;width:390px;height:165px;
    background:
      linear-gradient(to right,var(--paper) 0%,rgba(255,255,255,0) 45%),
      linear-gradient(to bottom,rgba(255,255,255,0) 55%,var(--paper) 100%),
      linear-gradient(160deg,var(--sky-tone) 0%,var(--page-tone-1) 45%,var(--page-tone-2) 75%,var(--page-tone-1) 100%);
  }
  .corner-accent{
    position:absolute;left:60px;top:58px;width:152px;height:33px;border-radius:6px;
    background:linear-gradient(to right,var(--blue-light),var(--accent-grey));
    opacity:.75;
  }

  .section-title{
    position:absolute;left:303px;top:92px;width:318px;
    font-size:34px;font-weight:400;line-height:40px;text-align:center;color:var(--ink);white-space:nowrap;
  }
  .section-rule{position:absolute;left:0;top:151px;width:927px;height:1px;background:var(--rule)}
  .section-bar{position:absolute;left:303px;top:133px;width:318px;height:18px;background:var(--blue)}

  .band-line{position:absolute;left:0;top:199px;width:927px;height:2px;background:var(--blue)}
  .tab{
    position:absolute;left:-10px;top:179px;width:366px;height:42px;
    background:linear-gradient(to bottom,var(--blue-light),var(--blue-dark));
    border:2px solid var(--paper);border-radius:0 14px 14px 0;
    box-shadow:0 0 0 1px var(--blue);
    color:#fff;font-size:33px;line-height:38px;padding-left:73px;white-space:nowrap;
  }

  .content{position:absolute;left:80px;top:229px;width:800px;font-size:21px;line-height:25px}
  .program-title{font-size:27.4px;font-weight:700;text-align:center;line-height:34px;margin-bottom:0}
  .content p{text-align:justify}
  .label{font-weight:700}
  .heading{text-decoration:underline}
  .gap{height:25px}
  .courses{display:grid;grid-template-columns:382px 1fr}

  .footer-rule{position:absolute;left:0;top:1156px;width:927px;height:1px;background:var(--rule)}
  .footer-text{position:absolute;right:34px;top:1168px;font-size:17px;color:var(--footer-ink);white-space:nowrap}
</style>
</head>
<body>
<div class="page">
  <div class="header-image" role="img" aria-label="Soft photo of an open book with turning pages"></div>
  <div class="corner-accent" role="img" aria-label="Small decorative accent in blue and grey"></div>

  <h1 class="section-title">ACADEMIC PROGRAMS</h1>
  <div class="section-rule"></div>
  <div class="section-bar"></div>

  <div class="band-line"></div>
  <div class="tab">GRADUATE DEGREE</div>

  <main class="content">
    <h2 class="program-title">Master of Business Administration (MBA) Degree</h2>
    <p>Redwell Institute's MBA program is designed to be flexible, cutting-edge and career minded. It is appropriate for all students with an undergraduate degree, whether in business or other industry area. The coursework not only prepares students for working in upper managerial positions, but also provides valuable knowledge and life tools useful for any profession.</p>
    <p>The program, while rigorous with a technical focus, exposes students to the environmental, social, political, and global economic conditions that produce the international market. The primary advantages of the MBA program at RWIB include small classroom sizes with ample opportunities for interaction with faculty through consultation and individual progress checks, and with classmates through group cooperation on projects in and outside of the classroom. In this manner and with a truly innovative system that keeps students up-to-date with market trends, RWIB creates a real business environment that's unlike any other MBA program.</p>
    <div><span class="label">Hours:</span> 6 hours per week</div>
    <div><span class="label">Length:</span> 8 weeks per course</div>
    <div class="label heading">Requirements:</div>
    <div>Bachelor Degree (with passing Calculus score)</div>
    <div class="gap"></div>

    <div class="heading">Required Courses:</div>
    <div class="courses">
      <span>ACCT 600 Financial Accounting</span><span>ACCT 601 Managerial Accounting</span>
      <span>MKT 601 Marketing Principles</span><span>BUS 601 Statistics</span>
      <span>COMP 603 Information Technology</span><span>BUS 603 Human Resources Management</span>
      <span>BUS 604 Introduction to Finance</span><span>BUS 605 Economic Fundamentals</span>
    </div>
    <div class="gap"></div>

    <div class="heading">Elective Courses: (Choose 3)</div>
    <div class="courses">
      <span>BUS 600 Starting Your Own Business</span><span>MKT 602 Marketing Research</span>
      <span>MKT 607/ACCT 607 Internship</span><span>MKT 606 E-Commerce</span>
      <span>ACCT 605 Introduction to Investments</span><span>BUS 602 Fundamentals of Importing &amp; Exporting</span>
    </div>
    <div class="gap"></div>

    <div class="heading">Learning Outcome:</div>
    <p>Highlights of the MBA program include a real-world business project with a company abroad, design of a professional and working business plan for investors, creation and maintenance of a career-management portfolio. To be sure, this a serious program that prepares graduates to be leaders of their industries, to think with a global perspective, use extensive research, and put their practices into action.</p>
  </main>

  <div class="footer-rule"></div>
  <div class="footer-text">15::: REDWELL INSTITUTE</div>
</div>
</body>
</html>
```